Asphalt Driveway Billboard Design

We need a billboard designed for an Asphalt & Concrete Company in Minnesota. We want to advertise Asphalt Driveways on this billboard! Logo is uploaded below. Our website is pinecrest-paving.com for more information.

```html
<!DOCTYPE html>
<html lang="en">
<head>
<meta charset="utf-8">
<title>Pinecrest – Residential Asphalt Driveway Billboard</title>
<link rel="stylesheet" href="https://fonts.googleapis.com/css2?family=Krona+One&family=Poppins:wght@500;700&family=Barlow+Semi+Condensed:wght@700&display=swap">
<style>
  :root {
    --page: #e6e6e8;
    --blue-deep: #1462a6;
    --blue-light: #3ea3d3;
    --accent-blue: #2b8fd0;
    --ink: #232325;
    --grey: #a6a7ab;
    --white: #ffffff;
    --sky: #5f9fdc;
    --house: #cdbf9f;
    --drive: #2e3033;
    --lawn: #5f9a3a;
  }
  html, body {
    margin: 0;
    width: 1121px;
    height: 1200px;
    overflow: hidden;
    background: var(--page);
  }
  .canvas {
    width: 1121px;
    height: 1200px;
    display: flex;
    align-items: center;
    justify-content: center;
  }
  .billboard {
    width: 1040px;
    height: 303px;
    box-shadow: 0 8px 18px rgba(0,0,0,0.25);
    display: block;
  }
  .headline { font-family: "Krona One", sans-serif; fill: var(--white); }
  .phone-number { font-family: "Poppins", sans-serif; font-weight: 700; fill: var(--white); }
  .offer { font-family: "Barlow Semi Condensed", sans-serif; font-weight: 700; fill: var(--white); }
  .web-address { font-family: "Poppins", sans-serif; font-weight: 500; fill: var(--white); }
  .brand-name { font-family: "Krona One", sans-serif; fill: var(--ink); }
</style>
</head>
<body>
<main class="canvas">
  <svg class="billboard" viewBox="0 0 1310 382" xmlns="http://www.w3.org/2000/svg">
    <defs>
      <linearGradient id="blueBand" x1="0" y1="0" x2="1" y2="0">
        <stop offset="0" stop-color="var(--blue-deep)"/>
        <stop offset="0.6" stop-color="var(--blue-light)"/>
        <stop offset="1" stop-color="var(--blue-deep)"/>
      </linearGradient>
      <linearGradient id="photoTones" x1="0" y1="0" x2="0" y2="1">
        <stop offset="0" stop-color="var(--sky)"/>
        <stop offset="0.35" stop-color="#a9c6e6"/>
        <stop offset="0.5" stop-color="var(--house)"/>
        <stop offset="0.75" stop-color="#8b7a66"/>
        <stop offset="0.85" stop-color="var(--drive)"/>
        <stop offset="1" stop-color="var(--drive)"/>
      </linearGradient>
    </defs>

    <rect class="board-base" x="0" y="0" width="1310" height="382" fill="var(--white)"/>

    <!-- headline band -->
    <path class="headline-band" d="M0 0 L830 0 Q792 80 782 170 L0 170 Z" fill="url(#blueBand)"/>
    <text class="headline" x="42" y="95" font-size="66" textLength="718" lengthAdjust="spacingAndGlyphs">RESIDENTIAL</text>
    <text class="headline" x="46" y="153" font-size="40" textLength="714" lengthAdjust="spacingAndGlyphs">ASPHALT DRIVEWAY</text>

    <!-- contact band -->
    <rect class="phone-band" x="0" y="176" width="422" height="64" fill="var(--ink)"/>
    <rect class="offer-band" x="422" y="176" width="360" height="64" fill="var(--grey)"/>
    <g class="phone-icon" transform="translate(68 208)">
      <circle r="19" fill="var(--accent-blue)"/>
      <circle r="14" fill="none" stroke="var(--ink)" stroke-width="2"/>
      <path d="M-6 -8 q-3 2 -1 8 q3 7 10 9 q4 1 6 -2 l-4 -4 l-3 2 q-4 -2 -6 -6 l2 -3 z" fill="var(--ink)"/>
    </g>
    <text class="phone-number" x="100" y="225" font-size="42" textLength="300" lengthAdjust="spacingAndGlyphs">763-555-0142</text>
    <text class="offer" x="441" y="223" font-size="40" textLength="305" lengthAdjust="spacingAndGlyphs">FREE ESTIMATE</text>

    <!-- brand -->
    <circle class="brand-mark" cx="108" cy="287" r="16" fill="var(--accent-blue)"/>
    <text class="brand-name" x="108" y="330" font-size="20" text-anchor="middle" textLength="128" lengthAdjust="spacingAndGlyphs">PINECREST</text>

    <!-- accent line and web bar -->
    <rect class="accent-line" x="283" y="268" width="510" height="5" fill="var(--accent-blue)"/>
    <path class="side-sweep" d="M830 0 L1310 0 L1310 382 L200 382 L283 280 L790 280 Q778 130 830 0 Z" fill="var(--ink)"/>
    <text class="web-address" x="283" y="328" font-size="34" textLength="465" lengthAdjust="spacingAndGlyphs">www.pinecrest-paving.com</text>

    <!-- swooshes framing the photo -->
    <path class="white-swoosh" d="M940 0 L1310 0 L1310 382 L860 382 Q810 300 820 200 Q835 80 940 0 Z" fill="var(--white)"/>
    <path class="grey-swoosh" d="M950 0 L1310 0 L1310 382 L962 382 Q848 300 850 190 Q855 80 950 0 Z" fill="var(--grey)"/>
    <path class="photo-frame" d="M955 0 L1310 0 L1310 382 L978 382 Q868 310 872 200 Q878 80 955 0 Z" fill="var(--white)"/>
    <path class="house-photo" role="img" aria-label="Photo of a two-storey suburban house with a fresh black asphalt driveway and green lawn under a blue sky"
          d="M965 0 L1310 0 L1310 382 L988 382 Q880 310 882 200 Q888 80 965 0 Z" fill="url(#photoTones)"/>
  </svg>
</main>
</body>
</html>
```